Brightmill Data Works

Our company is about IT hardwares and IT solutions. IT hardware such as PC, RAMS, storage and servers. IT solutions such as project management, BA. We are also selling new technology too.

Target Market(s)

Consumer, Small to Medium Business, Corporate

Requirements
Must have
• The business card must have the following:
• Name:
• Title:
• Contact Number:
• Email address:
• Website:
• Color: Must match the logo color upgrade

```html
<!DOCTYPE html>
<html lang="en">
<head>
<meta charset="utf-8">
<title>Brightmill Data Works — Business Card</title>
<link rel="stylesheet" href="https://fonts.googleapis.com/css2?family=Lato:wght@400;700;900&display=swap">
<style>
  :root {
    --stage: #2a2a2b;
    --card-dark: #1c1c1d;
    --card-light: #ffffff;
    --ink: #2b2b2b;
    --ink-soft: #3a3a3a;
    --accent: #d98b2b;
    --accent-deep: #c7761d;
    --band-dark: #262626;
  }
  * { box-sizing: border-box; margin: 0; padding: 0; }
  html, body { width: 1200px; height: 900px; overflow: hidden; }
  body {
    background: var(--stage);
    font-family: "Lato", sans-serif;
    position: relative;
  }
  .card {
    position: absolute;
    width: 640px;
    height: 366px;
    border-radius: 2px;
    overflow: hidden;
  }
  .card--back { left: 280px; top: 60px; background: var(--card-dark); }
  .card--front { left: 280px; top: 474px; background: var(--card-light); }

  .brand {
    display: flex;
    align-items: center;
    gap: 14px;
  }
  .brand__dot {
    width: 34px; height: 34px;
    border-radius: 50%;
    background: var(--accent);
    flex: none;
  }
  .brand__name {
    font-weight: 900;
    text-transform: uppercase;
    letter-spacing: 1px;
    line-height: 1.05;
  }

  .card--back .brand {
    position: absolute;
    left: 0; right: 0; top: 120px;
    justify-content: center;
  }
  .card--back .brand__name { color: #ffffff; font-size: 34px; }
  .card--back .website {
    position: absolute;
    left: 0; right: 0; top: 270px;
    text-align: center;
    color: #ffffff;
    font-size: 15px;
    letter-spacing: 0.5px;
  }

  .card--front .brand {
    position: absolute;
    right: 56px; top: 60px;
  }
  .card--front .brand__name { color: var(--ink); font-size: 30px; }

  .rule {
    position: absolute;
    left: 60px; right: 90px; top: 196px;
    height: 2px;
    background: var(--accent);
  }
  .person { position: absolute; left: 60px; top: 162px; }
  .person__name { color: var(--accent); font-weight: 700; font-size: 26px; }
  .person__title {
    position: absolute; top: 42px; left: 0;
    color: var(--ink); font-size: 16px; white-space: nowrap;
  }
  .contacts {
    position: absolute; left: 60px; top: 238px;
    list-style: none;
  }
  .contacts li {
    display: flex; align-items: center; gap: 12px;
    color: var(--ink-soft); font-size: 15px; line-height: 24px;
  }
  .contacts svg { width: 14px; height: 14px; fill: var(--accent); flex: none; }
  .address {
    position: absolute; right: 60px; top: 270px;
    text-align: right; color: var(--ink); font-size: 15px; line-height: 21px;
  }
  .edge-bands { position: absolute; left: 0; bottom: 0; width: 640px; height: 16px; }
</style>
</head>
<body>
  <section class="card card--back" aria-label="Card back">
    <div class="brand">
      <span class="brand__dot"></span>
      <span class="brand__name">Brightmill<br>Data Works</span>
    </div>
    <p class="website">www.brightmilldata.com</p>
  </section>

  <section class="card card--front" aria-label="Card front">
    <div class="brand">
      <span class="brand__dot"></span>
      <span class="brand__name">Brightmill<br>Data Works</span>
    </div>

    <div class="person">
      <p class="person__name">Dana Whitford</p>
      <p class="person__title">Manager</p>
    </div>
    <div class="rule"></div>

    <ul class="contacts">
      <li>
        <svg viewBox="0 0 16 16" aria-hidden="true"><path d="M3.6 1l2.6 3-1.5 1.6c.9 2 2.5 3.6 4.6 4.6L10.9 8.7l3.1 2.6-1.3 2.7C6.8 14 2 9.2 1 3.3z"/></svg>
        555 014 6800
      </li>
      <li>
        <svg viewBox="0 0 16 16" aria-hidden="true"><path d="M4 1h8v4H4zM1 6h14v6h-3v3H4v-3H1zm4 4v3h6v-3z"/></svg>
        555 014 6801
      </li>
      <li>
        <svg viewBox="0 0 16 16" aria-hidden="true"><path d="M1 3h14v1L8 9 1 4zm0 3l7 5 7-5v7H1z"/></svg>
        info@brightmilldata.com
      </li>
      <li>
        <svg viewBox="0 0 16 16" aria-hidden="true"><path d="M8 1a7 7 0 100 14A7 7 0 008 1zm0 1.5c.8 1 1.4 2.3 1.6 4.5H6.4C6.6 4.8 7.2 3.5 8 2.5zM2.6 7h2.3c.1-1.6.5-3 1.1-4A5.5 5.5 0 002.6 7zm8.5 0h2.3A5.5 5.5 0 0010 3c.6 1 1 2.4 1.1 4zM2.6 9A5.5 5.5 0 006 13c-.6-1-1-2.4-1.1-4zm3.8 0c.2 2.2.8 3.5 1.6 4.5.8-1 1.4-2.3 1.6-4.5zm4.7 0c-.1 1.6-.5 3-1.1 4a5.5 5.5 0 003.4-4z"/></svg>
        www.brightmilldata.com
      </li>
    </ul>

    <p class="address">48 Alder Row<br>Austin, TX 78701</p>

    <svg class="edge-bands" viewBox="0 0 640 16" preserveAspectRatio="none" aria-hidden="true">
      <polygon points="0,10 478,10 470,16 0,16" fill="var(--band-dark)"/>
      <polygon points="486,0 640,0 640,16 472,16" fill="var(--accent)"/>
    </svg>
  </section>
</body>
</html>
```